University Student Business Card

Looking for a professional university student business card. Student is studying business with a focus on marketing. Some combination using a monogram and/or full name on the front with full name, university details and contact information on the back. Card should be modern design for a young professional. Prefer use of royal blue, black and white but am open to other uses of colour palette if it reinforces young/trendy style. Initials for a monogram are: KR. Full details will be provided in private consultation with designer(s).

Target Market(s)

Professional business people, marketers, advertisers, consultants

Industry/Entity Type

Business, marketing

Contact Information for Business Card

Monogram or personal logo, full name, university name, program of study, phone number, email address, pathfolio address

Other font styles liked:
• Open to suggestion to fulfill above requirements

Colors
0054AA
0677BA
7BADD7
CADEEF
E8F1F8

Requirements
Must have
• Monogram using letters K and R, and incorporate the business card details listed in the brief (specific details including personal contact info will be shared with successful designer to ensure privacy)
Nice to have
• Personal brand using monogram or personal logo (not a business logo)

```html
<!DOCTYPE html>
<html lang="en">
<head>
<meta charset="utf-8">
<title>KR Student Business Card</title>
<link rel="stylesheet" href="https://fonts.googleapis.com/css2?family=Montserrat:wght@400;500;700;800&display=swap">
<style>
  :root {
    --navy: #00172f;
    --royal: #0054aa;
    --ocean: #0677ba;
    --white: #ffffff;
    --ink: #1c1c1c;
    --faint: #e6e7ea;
    --rule: #c9ccd2;
    --backdrop: #2b2d31;
  }
  * { box-sizing: border-box; margin: 0; padding: 0; }
  html, body { width: 1200px; height: 1015px; overflow: hidden; }
  body {
    background: var(--backdrop);
    font-family: "Montserrat", Arial, sans-serif;
    position: relative;
  }
  .card {
    position: absolute;
    width: 640px;
    height: 366px;
    overflow: hidden;
    box-shadow: 0 14px 30px rgba(0,0,0,.45);
  }
  .card svg.swoosh { position: absolute; inset: 0; width: 100%; height: 100%; }
  .card-front { left: 80px; top: 90px; background: var(--navy); color: var(--white); }
  .card-back { left: 480px; top: 560px; background: var(--white); color: var(--ink); }

  .monogram {
    position: absolute;
    font-weight: 800;
    letter-spacing: -2px;
    line-height: 1;
  }
  .card-front .monogram { right: 70px; top: 40px; font-size: 90px; color: var(--white); }
  .card-back .monogram { right: 60px; top: 22px; font-size: 130px; color: var(--faint); }

  .identity { position: absolute; left: 48px; top: 150px; }
  .person-name { color: var(--ocean); font-weight: 500; font-size: 22px; letter-spacing: .5px; text-transform: uppercase; }
  .person-role { font-size: 15px; margin-top: 4px; }
  .divider { width: 150px; height: 1px; background: rgba(255,255,255,.25); margin: 12px 0; }
  .profile { display: flex; align-items: center; gap: 10px; font-size: 15px; }
  .profile-dot { width: 22px; height: 22px; border-radius: 50%; background: var(--ocean); }

  .institution { position: absolute; left: 48px; top: 80px; }
  .institution-name { color: var(--royal); font-weight: 700; font-size: 26px; letter-spacing: 1px; text-transform: uppercase; }
  .card-back .divider { background: var(--rule); width: 170px; }
  .address { font-size: 14px; line-height: 1.4; }
  .contact-list { list-style: none; font-size: 14px; line-height: 1.55; }
  .contact-list li { display: flex; align-items: center; gap: 8px; }
  .contact-list svg { width: 14px; height: 14px; flex: none; }
  .icon-fill { fill: var(--royal); }
  .icon-line { fill: none; stroke: var(--royal); stroke-width: 2.4; stroke-linejoin: round; }
</style>
</head>
<body>

<section class="card card-front" aria-label="Card front">
  <svg class="swoosh" viewBox="0 0 640 366" aria-hidden="true">
    <path fill="var(--royal)" d="M30 366 C70 250 250 220 420 190 C540 168 600 130 575 95 C625 135 580 205 440 228 C280 258 110 285 42 366 Z"/>
  </svg>
  <div class="monogram">KR</div>
  <div class="identity">
    <p class="person-name">Marcus Ellery</p>
    <p class="person-role">Business Marketing</p>
    <div class="divider"></div>
    <p class="profile"><span class="profile-dot"></span>pathfolio.com/name</p>
  </div>
</section>

<section class="card card-back" aria-label="Card back">
  <svg class="swoosh" viewBox="0 0 640 366" aria-hidden="true">
    <path fill="var(--royal)" d="M90 366 C130 300 260 275 420 250 C540 230 610 200 590 165 C640 195 610 255 460 278 C300 302 150 322 104 366 Z"/>
  </svg>
  <div class="monogram">KR</div>
  <div class="institution">
    <p class="institution-name">University Name</p>
    <div class="divider"></div>
    <p class="address">421, Address line goes here<br>45452, Country Name</p>
    <div class="divider"></div>
    <ul class="contact-list">
      <li><svg viewBox="0 0 24 24"><path class="icon-fill" d="M6.6 10.8a15 15 0 0 0 6.6 6.6l2.2-2.2a1 1 0 0 1 1-.25 11 11 0 0 0 3.6.6 1 1 0 0 1 1 1V20a1 1 0 0 1-1 1A17 17 0 0 1 3 4a1 1 0 0 1 1-1h3.5a1 1 0 0 1 1 1 11 11 0 0 0 .6 3.6 1 1 0 0 1-.25 1z"/></svg>055-410 872 316</li>
      <li><svg viewBox="0 0 24 24"><path class="icon-line" d="M3 6h18v12H3z M3 6l9 7 9-7"/></svg>hello@kreller.net</li>
      <li><svg viewBox="0 0 24 24"><circle class="icon-line" cx="12" cy="12" r="9"/><path class="icon-line" d="M3 12h18 M12 3c-4 5-4 13 0 18 M12 3c4 5 4 13 0 18"/></svg>www.kreller.net</li>
    </ul>
  </div>
</section>

</body>
</html>
```